Request for Business Card Design

Hi. My name is Marlene, I am looking for a new business card design for my company, Quarrow Signal Instruments, LLC. I really like the design you did for Tarsel Venture and was hoping you could do something similar using our full logo and our mark. I am also open to any raised texture design using our mark. I have attached our full logo, which would need to be somewhere on the card, as well as the mark in both outline and full form, as well as our brand colors / guide. The card does not have to be white, as long as our logo and mark appear. I actually like darker colored business cards more, but am open to all options. If you are interested in working with me, please let me know. We would also take the business card design into letterhead design if you can do that.

```html
<!DOCTYPE html>
<html lang="en">
<head>
<meta charset="UTF-8">
<title>Quarrow Signal Instruments — Business Card</title>
<link href="https://fonts.googleapis.com/css2?family=Montserrat:wght@400;500;700&display=swap" rel="stylesheet">
<style>
  :root {
    --page: #2a2a2c;
    --card: #141415;
    --card-edge: #1d9fc4;
    --accent: #1aa0cc;
    --ink: #f2f2f2;
    --ink-soft: #d8d8d8;
    --relief-dark: #1b1b1d;
    --relief-light: #5a5a5e;
  }
  * { box-sizing: border-box; margin: 0; padding: 0; }
  html, body { width: 1200px; height: 900px; overflow: hidden; }
  body {
    background: var(--page);
    font-family: "Montserrat", sans-serif;
    display: flex;
    flex-direction: column;
    align-items: center;
    justify-content: center;
    gap: 60px;
  }
  .card {
    position: relative;
    width: 630px;
    height: 360px;
    background: var(--card);
    border-radius: 22px;
    overflow: hidden;
    border-left: 3px solid var(--card-edge);
    border-bottom: 3px solid var(--card-edge);
  }
  .brand {
    display: flex;
    align-items: center;
    gap: 14px;
  }
  .brand-dot {
    width: 34px;
    height: 34px;
    border-radius: 50%;
    background: var(--accent);
    flex: none;
  }
  .brand-name {
    color: var(--ink);
    font-weight: 700;
    font-size: 19px;
    letter-spacing: 1px;
    text-transform: uppercase;
    line-height: 1.15;
  }
  .relief {
    position: absolute;
    background: radial-gradient(circle at 30% 30%, var(--relief-light), var(--relief-dark) 70%);
  }

  /* Front */
  .card-front .brand { position: absolute; left: 42px; top: 58px; }
  .card-front .relief {
    right: 0; top: 0;
    width: 290px; height: 170px;
    border-bottom-left-radius: 170px;
    opacity: .55;
  }
  .holder { position: absolute; left: 42px; top: 150px; }
  .holder-name { color: var(--accent); font-weight: 700; font-size: 26px; }
  .holder-role { color: var(--ink-soft); font-size: 14px; margin-top: 2px; }
  .address { color: var(--ink); font-size: 14px; line-height: 1.4; margin-top: 20px; }
  .contacts { list-style: none; margin-top: 16px; }
  .contacts li {
    display: flex; align-items: center; gap: 10px;
    color: var(--ink); font-size: 14px; line-height: 1.55;
  }
  .contacts svg { width: 13px; height: 13px; fill: var(--accent); flex: none; }

  /* Back */
  .card-back .relief {
    left: 0; bottom: 0;
    width: 360px; height: 300px;
    border-top-right-radius: 300px;
    opacity: .7;
  }
  .card-back .brand { position: absolute; right: 40px; bottom: 54px; }
  .card-back .brand-name { font-size: 22px; }
</style>
</head>
<body>

  <section class="card card-front">
    <div class="relief" role="img" aria-label="Raised embossed brand mark decoration"></div>
    <div class="brand">
      <span class="brand-dot"></span>
      <span class="brand-name">Quarrow Signal<br>Instruments</span>
    </div>
    <div class="holder">
      <p class="holder-name">Dorian Vale</p>
      <p class="holder-role">Owner</p>
      <p class="address">1180 Ridgeview Court<br>Alder Falls, CO 80417</p>
      <ul class="contacts">
        <li><svg viewBox="0 0 16 16"><path d="M3 1h3l1.5 4-2 1.2a9 9 0 0 0 4.3 4.3L11 8.5l4 1.5v3a2 2 0 0 1-2 2A12 12 0 0 1 1 3a2 2 0 0 1 2-2z"/></svg>+001 555 210 4830</li>
        <li><svg viewBox="0 0 16 16"><path d="M1 3h14v10H1zM2 4.2v.3l6 4 6-4v-.3z"/></svg>info@quarrowsignal.com</li>
        <li><svg viewBox="0 0 16 16"><circle cx="8" cy="8" r="7"/></svg>www.quarrowsignal.com</li>
      </ul>
    </div>
  </section>

  <section class="card card-back">
    <div class="relief" role="img" aria-label="Large raised embossed brand mark decoration"></div>
    <div class="brand">
      <span class="brand-dot"></span>
      <span class="brand-name">Quarrow Signal<br>Instruments</span>
    </div>
  </section>

</body>
</html>
```